larkforge website

commerce website to sell cookeries, brackets, mailboxes and to show off homes built. Modern Steel in design see marlo cycles web page to be like: https://www.marlocycles-demo.com/en/ sorry its bright nest hosting word press divi

must be able to add products to page

Target Market(s)

mainly western states of U.S.

Industry/Entity Type

Building Product

Coding

Coded - Design and coding required

Number of Pages Required

3 page

Font styles to use
Sans Serif

Colors

Designer to choose colors to be used in the design.

Requirements
Must have
• customers to be able to order products from page
• bright nest hosting word press divi

```html
<!DOCTYPE html>
<html lang="en">
<head>
<meta charset="utf-8">
<title>Larkforge</title>
<link rel="stylesheet" href="https://fonts.googleapis.com/css2?family=Fira+Sans:wght@300;400;600;700&family=Open+Sans:wght@400;600;700&display=swap">
<style>
  :root{
    --brand:#4b5b88;
    --brand-dark:#2f3a5c;
    --ink:#2b2b2b;
    --muted:#6f6f6f;
    --field:#ececec;
    --white:#ffffff;
    --hero-top:#3a4a66;
    --hero-bottom:#1f2a40;
  }
  html,body{margin:0;padding:0;overflow:hidden;background:var(--white);}
  .page{position:relative;width:1200px;height:4024px;overflow:hidden;font-family:"Open Sans",sans-serif;color:var(--ink);}
  .abs{position:absolute;}
  .heading{font-family:"Fira Sans",sans-serif;}
  .btn{position:absolute;display:flex;align-items:center;justify-content:center;border-radius:20px;background:var(--brand);color:var(--white);font:700 11px "Open Sans",sans-serif;letter-spacing:.5px;}
  /* hero */
  .hero-bg{left:0;top:0;width:1200px;height:680px;}
  .brand-mark{left:161px;top:42px;display:flex;align-items:center;gap:10px;color:var(--white);font:600 28px "Fira Sans",sans-serif;letter-spacing:1px;}
  .brand-mark i{display:block;width:18px;height:18px;border-radius:50%;background:var(--white);}
  .nav{top:36px;color:var(--white);font:700 13px "Open Sans",sans-serif;letter-spacing:.3px;}
  .nav-active::after{content:"";position:absolute;left:50%;top:22px;width:18px;height:2px;margin-left:-9px;background:var(--white);}
  .cart{left:994px;top:23px;width:44px;height:44px;border-radius:50%;background:var(--white);}
  .hero-title{left:0;width:1200px;top:212px;text-align:center;color:var(--white);font:300 62px "Fira Sans",sans-serif;letter-spacing:1px;}
  .hero-title b{font-weight:700;}
  .hero-copy{left:330px;width:540px;top:296px;text-align:center;color:var(--white);font-size:13.5px;line-height:22px;}
  /* features */
  .eyebrow{left:0;width:1200px;top:677px;text-align:center;font:400 19px "Fira Sans",sans-serif;color:#444;}
  .section-title{left:0;width:1200px;text-align:center;font:700 35px "Fira Sans",sans-serif;color:var(--brand);}
  .rule{left:319px;top:766px;width:562px;height:1px;background:#bdbdbd;}
  .icon-badge{width:60px;height:60px;border-radius:50%;background:var(--brand);}
  .icon-badge svg{position:absolute;left:15px;top:15px;}
  .product-name{font:600 20px "Fira Sans",sans-serif;color:#222;letter-spacing:.5px;}
  .product-copy{width:330px;font-size:11.5px;line-height:22.5px;color:var(--muted);}
  .right{text-align:right;}
  .shot{border-radius:8px;}
  /* welcome */
  .welcome-kicker{left:0;width:1200px;top:1833px;text-align:center;color:var(--white);font:300 20px "Fira Sans",sans-serif;}
  .welcome-title{left:0;width:1200px;top:1868px;text-align:center;color:var(--white);font:700 35px "Fira Sans",sans-serif;letter-spacing:1px;}
  .welcome-copy{left:330px;width:540px;top:1920px;text-align:center;color:var(--white);font-size:12.5px;line-height:23px;}
  /* testimonials */
  .card{width:264px;height:188px;background:var(--white);box-shadow:0 0 8px rgba(0,0,0,.18);}
  .card p{position:absolute;left:17px;top:14px;width:190px;margin:0;font-size:11px;line-height:23px;color:var(--muted);}
  .card .quote{position:absolute;right:16px;top:40px;font:700 44px "Fira Sans",sans-serif;color:#cfcfcf;line-height:44px;}
  .card .avatar{position:absolute;left:18px;top:96px;width:74px;height:74px;border-radius:50%;background:linear-gradient(135deg,#a9b0bb,#5a6170);}
  .card .name{position:absolute;left:106px;top:114px;font:600 16px "Fira Sans",sans-serif;color:#222;}
  .card .stars{position:absolute;left:106px;top:138px;font-size:12px;letter-spacing:4px;color:#9a9a9a;}
  /* newsletter */
  .news-title{left:620px;width:417px;top:2905px;text-align:right;color:var(--white);font:600 35px "Fira Sans",sans-serif;line-height:51px;}
  .news-input{left:664px;top:3034px;width:373px;height:44px;background:var(--white);border-radius:3px;}
  .news-input span{position:absolute;left:22px;top:14px;font-size:12px;color:#555;}
  /* contact */
  .contact-title{left:561px;width:478px;top:3330px;text-align:center;font:600 35px "Fira Sans",sans-serif;color:#333;}
  .field{background:var(--field);}
  .field span{position:absolute;left:10px;top:11px;font-size:11px;color:#777;}
  /* footer */
  .foot-head{font:600 22px "Fira Sans",sans-serif;color:var(--white);letter-spacing:.5px;}
  .foot-text{font-size:11px;line-height:16px;color:var(--white);}
  .foot-list{margin:0;padding:0;list-style:none;font-size:11px;color:var(--white);}
  .foot-list li{height:26.3px;}
</style>
</head>
<body>
<div class="page">

  <!-- HERO -->
  <svg class="abs hero-bg" viewBox="0 0 1200 680" role="img" aria-label="Photo of a modern glass house at dusk with a lounge and fire pit">
    <defs>
      <linearGradient id="heroFill" x1="0" y1="0" x2="0" y2="1">
        <stop offset="0" stop-color="#46566f"/>
        <stop offset=".55" stop-color="#2e3c58"/>
        <stop offset="1" stop-color="#243149"/>
      </linearGradient>
    </defs>
    <rect width="1200" height="680" fill="url(#heroFill)"/>
  </svg>
  <svg class="abs" style="left:0;top:530px" width="1200" height="160" viewBox="0 0 1200 160">
    <path d="M0 142 C300 40 450 9 600 9 C760 9 920 40 1200 142 L1200 160 L0 160 Z" fill="#fff"/>
    <line x1="600" y1="9" x2="600" y2="112" stroke="#9a9a9a" stroke-width="1"/>
    <circle cx="600" cy="9" r="8" fill="#fff" stroke="#9a9a9a"/>
    <circle cx="600" cy="9" r="3.5" fill="#333"/>
  </svg>

  <div class="abs brand-mark"><i></i>LARKFORGE</div>
  <div class="abs nav nav-active" style="left:577px">HOME</div>
  <div class="abs nav" style="left:639px">PRODUCTS</div>
  <div class="abs nav" style="left:731px">HOMES BUILT</div>
  <div class="abs nav" style="left:843px">ABOUT</div>
  <div class="abs nav" style="left:911px">CONTACT</div>
  <div class="abs cart">
    <svg width="44" height="44" viewBox="0 0 44 44"><path d="M13 15h3l3 11h10l2-8H17" fill="none" stroke="#4b5b88" stroke-width="2"/><circle cx="20" cy="29" r="1.6" fill="#4b5b88"/><circle cx="28" cy="29" r="1.6" fill="#4b5b88"/></svg>
  </div>
  <div class="abs hero-title"><b>LARK</b>FORGE</div>
  <div class="abs hero-copy">Lorem Ipsum is simply dummy text of the printing and typesetting industry. Lorem Ipsum has been the industry's standard dummy text ever since the 1500s.</div>
  <div class="btn" style="left:544px;top:359px;width:112px;height:36px;font-size:12px">LOG IN</div>

  <!-- FEATURES -->
  <div class="abs eyebrow">FEATURES</div>
  <div class="abs section-title" style="top:708px">OUR TOP PRODUCT</div>
  <div class="abs rule"></div>

  <div class="abs icon-badge" style="left:162px;top:842px">
    <svg width="30" height="30" viewBox="0 0 30 30"><circle cx="15" cy="15" r="12" fill="none" stroke="#fff" stroke-width="2"/><circle cx="15" cy="15" r="6" fill="none" stroke="#fff" stroke-width="2"/></svg>
  </div>
  <div class="abs product-name" style="left:247px;top:860px">STEEL COOKERY</div>
  <div class="abs product-copy" style="left:247px;top:896px">Lorem Ipsum is simply dummy text of the printing and typesetting industry.Lorem Ipsum is simply dummy text of the printing and typesetting industry.</div>
  <div class="btn" style="left:247px;top:984px;width:112px;height:35px">LEARN MORE</div>
  <div class="abs shot" role="img" aria-label="Round stone-topped fire table with woven steel base" style="left:664px;top:816px;width:247px;height:203px;background:radial-gradient(ellipse at 50% 35%,#bdbdbd 0,#9a9a9a 35%,#3d3d3d 60%,#fff 72%)"></div>

  <div class="abs shot" role="img" aria-label="Brushed steel handrail bracket" style="left:250px;top:1098px;width:242px;height:165px;background:radial-gradient(ellipse at 50% 50%,#d8d8d8 0,#b2b2b2 40%,#fff 70%)"></div>
  <div class="abs product-name right" style="left:655px;width:300px;top:1110px">BRACKETS</div>
  <div class="abs icon-badge" style="left:978px;top:1092px">
    <svg width="30" height="30" viewBox="0 0 30 30"><rect x="5" y="5" width="20" height="20" fill="none" stroke="#fff" stroke-width="2"/><path d="M9 9l12 12" stroke="#fff" stroke-width="2"/></svg>
  </div>
  <div class="abs product-copy right" style="left:625px;top:1147px">Lorem Ipsum is simply dummy text of the printing and typesetting industry.Lorem Ipsum is simply dummy text of the printing and typesetting industry.</div>
  <div class="btn" style="left:842px;top:1233px;width:113px;height:37px">LEARN MORE</div>

  <div class="abs icon-badge" style="left:162px;top:1345px">
    <svg width="30" height="30" viewBox="0 0 30 30"><rect x="4" y="8" width="22" height="15" fill="none" stroke="#fff" stroke-width="2"/><path d="M4 8l11 9 11-9" fill="none" stroke="#fff" stroke-width="2"/></svg>
  </div>
  <div class="abs product-name" style="left:247px;top:1363px">MAIL BOXES</div>
  <div class="abs product-copy" style="left:247px;top:1400px">Lorem Ipsum is simply dummy text of the printing and typesetting industry.Lorem Ipsum is simply dummy text of the printing and typesetting industry.</div>
  <div class="btn" style="left:247px;top:1488px;width:112px;height:35px">LEARN MORE</div>
  <div class="abs shot" role="img" aria-label="Galvanised steel mailbox" style="left:669px;top:1344px;width:281px;height:184px;background:linear-gradient(180deg,#d2d4d6,#8e9196 70%,#6c6f74);border-radius:90px 90px 6px 6px"></div>

  <!-- WELCOME BAND -->
  <svg class="abs" style="left:0;top:1578px" width="1200" height="642" viewBox="0 0 1200 642" role="img" aria-label="Photo of a modern house with dark cladding among palm trees">
    <defs>
      <linearGradient id="welcomeFill" x1="0" y1="0" x2="1" y2="1">
        <stop offset="0" stop-color="#3c4a38"/>
        <stop offset=".45" stop-color="#3f4b63"/>
        <stop offset="1" stop-color="#2a3043"/>
      </linearGradient>
    </defs>
    <path d="M0 0 C260 60 520 230 760 230 C960 230 1100 170 1200 132 L1200 532 C1000 600 800 640 640 640 C420 640 220 470 0 445 Z" fill="url(#welcomeFill)"/>
  </svg>
  <div class="abs welcome-kicker">Welcome To</div>
  <div class="abs welcome-title">LARKFORGE</div>
  <div class="abs welcome-copy">Lorem Ipsum is simply dummy text of the printing and typesetting industry. Lorem Ipsum has been the industry's standard dummy text ever since the 1500s, when an unknown printer took.</div>
  <div class="btn" style="left:544px;top:2009px;width:112px;height:35px">ABOUT US</div>

  <!-- TESTIMONIALS -->
  <div class="abs section-title" style="top:2282px">TESTIMONIAL</div>
  <div class="abs card" style="left:161px;top:2356px">
    <p>Lorem Ipsum is simply dummy text of the printing and typesetting industry.</p><div class="quote">”</div>
    <div class="avatar" role="img" aria-label="Customer portrait"></div><div class="name">Lorem</div><div class="stars">★★★★★</div>
  </div>
  <div class="abs card" style="left:466px;top:2356px">
    <p>Lorem Ipsum is simply dummy text of the printing and typesetting industry.</p><div class="quote">”</div>
    <div class="avatar" role="img" aria-label="Customer portrait"></div><div class="name">Lorem</div><div class="stars">★★★★★</div>
  </div>
  <div class="abs card" style="left:769px;top:2356px">
    <p>Lorem Ipsum is simply dummy text of the printing and typesetting industry.</p><div class="quote">”</div>
    <div class="avatar" role="img" aria-label="Customer portrait"></div><div class="name">Lorem</div><div class="stars">★★★★★</div>
  </div>

  <!-- NEWSLETTER -->
  <svg class="abs" style="left:0;top:2620px" width="1200" height="650" viewBox="0 0 1200 650">
    <defs>
      <linearGradient id="claddingFill" x1="0" y1="0" x2="1" y2="0">
        <stop offset="0" stop-color="#3a3c3f"/>
        <stop offset=".5" stop-color="#5a5c60"/>
        <stop offset="1" stop-color="#2e3033"/>
      </linearGradient>
    </defs>
    <path role="img" aria-label="Photo of dark steel wall cladding with glass sliding doors" d="M0 2 C220 -10 420 70 601 138 L601 600 C420 540 220 460 0 443 Z" fill="url(#claddingFill)"/>
    <path d="M601 262 C800 240 1000 190 1200 138 L1200 528 C1000 610 820 650 740 640 C690 634 640 612 601 600 Z" fill="#4b5b88"/>
  </svg>
  <div class="abs news-title">Keep Updated &amp; Get<br>Unlimited Descount</div>
  <div class="abs news-input"><span>Enter Your E-mail Address</span>
    <svg class="abs" style="left:338px;top:12px" width="22" height="20" viewBox="0 0 22 20"><path d="M1 9L21 1 16 19 10 12Z" fill="#4b5b88"/><path d="M10 12L21 1" stroke="#fff" stroke-width="1.2"/></svg>
  </div>
  <div class="btn" style="left:927px;top:3109px;width:110px;height:36px;background:var(--white);color:var(--brand-dark)">LEARN MORE</div>

  <!-- CONTACT -->
  <div class="abs" role="img" aria-label="Photo of a smiling woman in a light blazer pointing upward" style="left:172px;top:3336px;width:297px;height:398px;border-radius:140px 140px 20px 20px;background:linear-gradient(180deg,#6b4a36 0,#c9b8a8 45%,#d9d4cf 100%)"></div>
  <div class="abs contact-title">CONTACT US</div>
  <div class="abs field" style="left:561px;top:3397px;width:223px;height:36px"><span>First Name</span></div>
  <div class="abs field" style="left:816px;top:3397px;width:223px;height:36px"><span>Last Name</span></div>
  <div class="abs field" style="left:561px;top:3458px;width:223px;height:36px"><span>E-mail</span></div>
  <div class="abs field" style="left:816px;top:3458px;width:223px;height:36px"><span>Phone</span></div>
  <div class="abs field" style="left:561px;top:3517px;width:478px;height:74px"><span>Message</span></div>
  <div class="btn" style="left:744px;top:3616px;width:112px;height:36px;font-size:15px">SUBMIT</div>

  <!-- FOOTER -->
  <svg class="abs" style="left:0;top:3600px" width="1200" height="424" viewBox="0 0 1200 424">
    <path d="M0 10 C250 120 450 142 600 142 C760 142 960 110 1200 10 L1200 424 L0 424 Z" fill="#4b5b88"/>
  </svg>
  <div class="abs" style="left:164px;top:3830px;display:flex;align-items:center;gap:7px;color:var(--white);font:600 18px 'Fira Sans',sans-serif"><i style="display:block;width:12px;height:12px;border-radius:50%;background:#fff"></i>LARKFORGE</div>
  <div class="abs foot-text" style="left:164px;top:3891px">© Larkforge - 2020 All<br>Rights Reserved.</div>

  <div class="abs foot-head" style="left:388px;top:3798px">SITE MAP</div>
  <ul class="abs foot-list" style="left:388px;top:3863px">
    <li>HOME</li><li>PRODUCTS</li><li>HOMES BUILT</li><li>ABOUT</li><li>CONTACT</li>
  </ul>

  <div class="abs foot-head" style="left:600px;top:3798px">CONTACT US</div>
  <svg class="abs" style="left:598px;top:3862px" width="14" height="20" viewBox="0 0 14 20"><path d="M7 19C3 13 1 10 1 7a6 6 0 0 1 12 0c0 3-2 6-6 12z" fill="#fff"/><circle cx="7" cy="7" r="2.3" fill="#4b5b88"/></svg>
  <div class="abs foot-text" style="left:627px;top:3862px;width:160px">123 - lorem ipsum is text and dynamic text.</div>
  <svg class="abs" style="left:598px;top:3916px" width="18" height="18" viewBox="0 0 18 18"><path d="M4 1l3 4-2 2c1 3 3 5 6 6l2-2 4 3-2 3C8 17 1 10 1 3z" fill="#fff"/></svg>
  <div class="abs foot-text" style="left:627px;top:3917px">+(91) 555 010 2040</div>
  <svg class="abs" style="left:598px;top:3957px" width="20" height="16" viewBox="0 0 20 16"><path d="M1 6l9-5 9 5v9H1z" fill="none" stroke="#fff" stroke-width="1.6"/><path d="M1 6l9 6 9-6" fill="none" stroke="#fff" stroke-width="1.6"/></svg>
  <div class="abs foot-text" style="left:627px;top:3958px">info@larkforge.com</div>

  <div class="abs foot-head" style="left:892px;top:3798px">FOLLOW US</div>
  <ul class="abs foot-list" style="left:892px;top:3863px">
    <li>FACEPAGE</li><li>CHIRPER</li><li>LINKWORK</li><li>PICGRAM</li>
  </ul>

</div>
</body>
</html>
```